Design eines Hausetiketts für traditionelles Weingut
Zielgruppe
Wir das Familienweingut Brandauer in Gimbsheim/Rheinhessen sind ein traditionelles Weingut das seine Reben selbst kultiviert und die Weine auch selbst ausbaut. Wir haben jeden Schritt in der Weinherstellung selbst in der Hand und vermarkten den Wein dann an unsere Privatkunden. Unsere Kundenstruktur sieht folgendermaßen aus: Wir haben 100% Privatkunden die unseren Wein konsumieren. Da jetzt die nächste Generation in den Weinbaubetrieb einsteigt und auch Ideen hat möchten wir ein Hausetikett einführen. Im Moment haben wir noch sehr viele unterschiedliche Etiketten und kein Hausetikett. Da die Verlagsetiketten immer seltener zu unseren Vorstellungen passen, möchten wir hier auf diesem Wege ein Hausetikett anfertigen lassen. Generell möchten wir unseren Außenauftritt komplett modernisieren. Sie können sich über die Vielfalt in unserem Betrieb unter www.weingut-brandauer-beispiel.de einen Überblick verschaffen. Langfristig gesehen wollen wir aber unsere Weinkarte verkleinern.
Aufgabenstellung
Wir haben uns vor ca. 1,5 Jahren hier auf dieser Website bereits ein Logo designen lassen. Es wäre schön wenn man das Logo bei den Entwürfen für die Etiketten berücksichtigen würde. Das wäre aber KEIN MUSS. Auch wäre es gut wenn man das ,,Wein' bei unserem Namen weglassen könnte.
Das Etikett sollte aus Vorder-und Rückenetikett bestehen und edel wirken. Vorne sollte die Rebsorte und die Geschmacksangabe stehen. Der Rest sollte auf das Rückenetikett.
Das Vorderetikett sollte ein richtiger Eyecatcher sein und im Supermarkt z.B. aus vielen anderen herausstechen. Das wäre ganz wichtig.
Man kann bei den Farben unterscheiden in 3 Konzepte.
Literwein als einsteiger Wein
Dann die Gutsweine und zum Schluss die Lagenweine. Alles Farblich oder im design etwas abgesetzt.

```html
<!DOCTYPE html>
<html lang="de">
<head>
<meta charset="utf-8">
<title>Hausetikett Riesling trocken – Brandauer</title>
<link rel="stylesheet" href="https://fonts.googleapis.com/css2?family=Cormorant+Garamond:wght@500&family=Sacramento&family=Open+Sans:wght@400;700&family=Pathway+Gothic+One&display=swap">
<style>
  :root {
    --stage: #f1f0eb;
    --label-ink: #2a2d35;
    --paper: #ffffff;
    --gold: #a6784a;
  }
  * { margin: 0; padding: 0; box-sizing: border-box; }
  html, body {
    width: 1043px;
    height: 1200px;
    overflow: hidden;
    background: var(--stage);
  }
  .canvas {
    position: relative;
    width: 1043px;
    height: 1200px;
  }
  .front-label {
    position: absolute;
    left: 201px;
    top: 58px;
    width: 641px;
    height: 1084px;
    background: var(--paper);
    padding: 9px;
  }
  .front-label__field {
    position: relative;
    width: 100%;
    height: 100%;
    background: var(--label-ink);
  }
  .estate-mark {
    position: absolute;
    top: 118px;
    left: 0;
    right: 0;
    display: flex;
    justify-content: center;
    align-items: center;
    gap: 12px;
    font-family: "Open Sans", sans-serif;
    font-weight: 400;
    font-size: 26px;
    letter-spacing: 3px;
    color: var(--gold);
  }
  .estate-mark__dot {
    width: 16px;
    height: 16px;
    border-radius: 50%;
    background: var(--gold);
  }
  .claim {
    position: absolute;
    top: 300px;
    left: 0;
    right: 0;
    text-align: center;
    font-family: "Pathway Gothic One", sans-serif;
    font-size: 130px;
    line-height: 1;
    letter-spacing: 6px;
    color: var(--paper);
  }
  .name-band {
    position: absolute;
    left: -59px;
    right: -59px;
    top: 435px;
    height: 130px;
    background: var(--paper);
    display: flex;
    justify-content: center;
    align-items: center;
  }
  .name-band__name {
    font-family: "Cormorant Garamond", serif;
    font-weight: 500;
    font-size: 98px;
    line-height: 1;
    letter-spacing: -4px;
    color: var(--gold);
    padding-top: 6px;
  }
  .variety {
    position: absolute;
    top: 590px;
    left: 0;
    right: 0;
    height: 300px;
    display: flex;
    justify-content: center;
    align-items: center;
    font-family: "Sacramento", cursive;
    font-size: 170px;
    line-height: 1;
    color: var(--paper);
  }
  .taste {
    position: absolute;
    top: 890px;
    left: 0;
    right: 0;
    text-align: center;
    font-family: "Open Sans", sans-serif;
    font-weight: 400;
    font-size: 46px;
    line-height: 1;
    color: var(--paper);
  }
  .vintage {
    position: absolute;
    top: 960px;
    left: 0;
    right: 0;
    text-align: center;
    font-family: "Open Sans", sans-serif;
    font-weight: 700;
    font-size: 26px;
    line-height: 1;
    color: var(--paper);
  }
</style>
</head>
<body>
<main class="canvas">
  <section class="front-label" aria-label="Vorderetikett Riesling trocken">
    <div class="front-label__field">
      <div class="estate-mark">
        <span class="estate-mark__dot"></span>
        <span class="estate-mark__name">Brandauer</span>
      </div>
      <p class="claim">EIN ECHTER</p>
      <div class="name-band">
        <span class="name-band__name">BRANDAUER</span>
      </div>
      <p class="variety">Riesling</p>
      <p class="taste">trocken</p>
      <p class="vintage">2019</p>
    </div>
  </section>
</main>
</body>
</html>
```